Veltrano.co - Polar Expeditions Specialists

We need a modern, visually striking business card for Veltrano.co, a company specialized in selling expedition cruises to the most remote regions on Earth, with a focus on the Arctic and Antarctica. The design should instantly communicate that the cardholder is an expert in polar travel. Use clean, premium aesthetics with cool tones like icy blue and white, possibly incorporating polar imagery (ice, glaciers, penguins, etc.)

Attached the logo

Contact Information for Business Card

Feels high-end and trustworthy.. Visually memorable — encourages people to keep it

Colors
0054AA
0677BA
7BADD7
CADEEF
E8F1F8

Requirements
Must have
• ice, glaciers, penguins, montains
Nice to have
• modern, transparente,

```html
<!DOCTYPE html>
<html lang="en">
<head>
<meta charset="UTF-8">
<title>Veltrano.co – Business Card</title>
<link rel="stylesheet" href="https://fonts.googleapis.com/css2?family=Poppins:wght@300;400;600;700;800&display=swap">
<style>
  :root {
    --stage: #2c2c2c;
    --brand-blue: #3476b8;
    --brand-blue-soft: #5a92cc;
    --front-light: #5592cb;
    --front-deep: #3a7dbf;
    --ice: #e8f1f8;
    --white: #ffffff;
  }
  * { box-sizing: border-box; margin: 0; padding: 0; }
  html, body {
    width: 1200px; height: 1015px; overflow: hidden;
    background: var(--stage);
    font-family: "Poppins", sans-serif;
  }
  .card {
    position: absolute; left: 280px;
    width: 640px; height: 366px;
    overflow: hidden;
    box-shadow: 0 10px 24px rgba(0,0,0,.45);
  }
  .card--front { top: 100px; }
  .card--back { top: 549px; background: var(--white); }

  /* front */
  .front-scene {
    position: absolute; inset: 0;
    background:
      radial-gradient(ellipse 60% 40% at 45% 75%, rgba(232,241,248,.18), transparent 70%),
      linear-gradient(170deg, var(--front-light) 0%, #4e8ccb 45%, var(--front-deep) 100%);
  }
  .front-brand {
    position: absolute; inset: 0;
    display: flex; flex-direction: column; align-items: center; justify-content: center;
    color: var(--white);
    padding-top: 10px;
  }
  .brand-mark {
    width: 58px; height: 58px; border-radius: 50%;
    background: var(--white);
    margin-bottom: 16px;
  }
  .brand-name {
    font-weight: 800; font-size: 66px; line-height: 1; letter-spacing: -1px;
  }
  .brand-tagline {
    font-weight: 700; font-size: 19px; margin-top: 6px; letter-spacing: .3px;
  }

  /* back */
  .back-band {
    position: absolute; left: 0; right: 0; top: 210px; bottom: 0;
    background: var(--brand-blue);
  }
  .back-feature {
    position: absolute; left: 400px; top: 0; right: 0; bottom: 0;
    background:
      radial-gradient(ellipse 70% 55% at 60% 40%, var(--brand-blue) 0%, var(--brand-blue) 60%, var(--brand-blue-soft) 100%);
    border-left: 3px solid var(--white);
  }
  .back-brand {
    position: absolute; left: 44px; top: 92px;
    color: var(--brand-blue);
  }
  .back-brand .brand-name { font-size: 50px; }
  .back-brand .brand-tagline { font-size: 14px; font-weight: 600; margin-top: 2px; padding-left: 22px; }
  .holder {
    position: absolute; left: 44px; top: 226px; color: var(--white);
  }
  .holder-name { font-weight: 700; font-size: 24px; line-height: 1.1; }
  .holder-role { font-weight: 300; font-size: 18px; line-height: 1.2; }
  .contact-list { list-style: none; margin-top: 14px; }
  .contact-list li {
    display: flex; align-items: center; gap: 8px;
    font-weight: 300; font-size: 16px; line-height: 1.45;
  }
  .contact-list svg { width: 14px; height: 14px; flex: none; }
</style>
</head>
<body>

<section class="card card--front">
  <div class="front-scene" role="img" aria-label="Soft blue-tinted photograph of icebergs and glaciers in polar waters"></div>
  <div class="front-brand">
    <div class="brand-mark"></div>
    <div class="brand-name">Veltrano.co</div>
    <div class="brand-tagline">Polar Expeditions Specialists</div>
  </div>
</section>

<section class="card card--back">
  <div class="back-band"></div>
  <div class="back-feature" role="img" aria-label="Large blue silhouette illustration of polar wildlife with penguins"></div>
  <div class="back-brand">
    <div class="brand-name">Veltrano.co</div>
    <div class="brand-tagline">Polar Expeditions Specialists</div>
  </div>
  <div class="holder">
    <div class="holder-name">Marcus Hale</div>
    <div class="holder-role">Managing Director</div>
    <ul class="contact-list">
      <li>
        <svg viewBox="0 0 24 24" fill="none" stroke="#fff" stroke-width="2.2" stroke-linecap="round" stroke-linejoin="round"><path d="M5 3h4l2 5-2.5 1.5a11 11 0 0 0 6 6L16 13l5 2v4a2 2 0 0 1-2 2A16 16 0 0 1 3 5a2 2 0 0 1 2-2z"/></svg>
        044-987 654 321
      </li>
      <li>
        <svg viewBox="0 0 24 24" fill="none" stroke="#fff" stroke-width="2.2" stroke-linejoin="round"><rect x="2" y="5" width="20" height="14"/><path d="M2 5l10 8 10-8"/></svg>
        hello@veltranomail.com
      </li>
      <li>
        <svg viewBox="0 0 24 24" fill="none" stroke="#fff" stroke-width="2"><circle cx="12" cy="12" r="10"/><path d="M2 12h20M12 2a15 15 0 0 1 0 20M12 2a15 15 0 0 0 0 20"/></svg>
        www.veltranotrips.com
      </li>
    </ul>
  </div>
</section>

</body>
</html>
```